Business card for a new innovative and professional lawn care business

We need a business card design for a new lawn care business in Halifax NS Canada. We offer lawn services in Halifax & Bedford. Our services offered include lawn care, garden services, and property maintenance. We take pride in our work and are experienced at what we do. I would like to see a design that is double sided. On the backside I would like the something simple (maybe my logo preferably on blackround (linked below) with website link, Facebook page or something). The front I want to include contact info:
Morgan Pell
phone 902-555-0148
email - brookvaleyards.ca
facebook - Facebook.com/brookvaleyards
Instagram maybe ? - instagram.com/brookvaleyard
Serving Halifax and Bedford for 5 years?
I don't want it to have too much information as I will be passing them out in aim to visit website, or call !
We do want it to include lawn care, garden services and property maintenance.
Basic, catchy, and modern looking !
Logo attached below !

Target Market(s)

Passing business cards to everyone I meet or interact with.

Industry/Entity Type

Lawn Care

Contact Information for Business Card

Double sided with some basic information, with catchy colours and easy to look at.

Font styles to use
Sans Serif

Requirements
Must have
• Must be double sided and have :
• Name, Phone, Email, FB, Website, and 3 main services offered - lawn care, property maintenance, garden services
Nice to have
• Would be nice to have instagram link if it goes well on there
Should not have
• Don't want too much writing or images that are distracting

```html
<!DOCTYPE html>
<html lang="en">
<head>
<meta charset="utf-8">
<title>Brookvale Yards – Business Card</title>
<link rel="stylesheet" href="https://fonts.googleapis.com/css2?family=Lato:wght@400;700;900&display=swap">
<style>
  :root {
    --backdrop: #2b2b2b;
    --card-white: #f7f7f7;
    --card-white-edge: #e6e6e6;
    --leaf: #8cc63f;
    --leaf-deep: #6aa82a;
    --forest: #1f7a3a;
    --forest-dark: #0f5c2a;
    --ink-on-green: #ffffff;
    --web-ink: rgba(255,255,255,0.85);
  }
  * { margin: 0; padding: 0; box-sizing: border-box; }
  html, body { width: 1200px; height: 873px; overflow: hidden; }
  body {
    background: var(--backdrop);
    font-family: "Lato", sans-serif;
    position: relative;
  }
  .card {
    position: absolute;
    width: 540px;
    height: 309px;
    border-radius: 18px;
    overflow: hidden;
    background: linear-gradient(160deg, #ffffff 0%, var(--card-white) 55%, var(--card-white-edge) 100%);
    box-shadow: 0 10px 30px rgba(0,0,0,0.5);
  }
  .card--services { left: 40px; top: 282px; }
  .card--contact  { left: 620px; top: 282px; }
  .card__band { position: absolute; inset: 0; width: 100%; height: 100%; }

  .brand {
    position: absolute;
    display: flex;
    align-items: center;
    gap: 10px;
    color: var(--forest);
    font-weight: 900;
    font-size: 34px;
    line-height: 1.1;
    letter-spacing: 1px;
    text-transform: uppercase;
    white-space: nowrap;
  }
  .brand__dot {
    width: 26px; height: 26px; border-radius: 50%;
    background: var(--leaf);
    flex: none;
  }
  .card--services .brand { left: 0; right: 0; top: 72px; justify-content: center; }
  .card--contact .brand { left: 0; right: 0; top: 86px; justify-content: center; font-size: 30px; }

  .tagline {
    position: absolute;
    left: 0; right: 0; top: 136px;
    text-align: center;
    color: var(--forest);
    font-weight: 700;
    font-size: 14px;
  }
  .services {
    position: absolute;
    left: 0; right: 0; bottom: 28px;
    display: flex;
    justify-content: center;
    gap: 28px;
    list-style: none;
    color: var(--ink-on-green);
    font-weight: 700;
    font-size: 16px;
  }
  .services li { display: flex; align-items: center; gap: 7px; }
  .services li::before {
    content: ""; width: 8px; height: 8px; border-radius: 50%;
    background: var(--ink-on-green);
  }

  .owner {
    position: absolute; left: 0; right: 0; top: 26px;
    text-align: center;
  }
  .owner__name { color: var(--leaf-deep); font-weight: 900; font-size: 18px; text-transform: uppercase; letter-spacing: 0.5px; }
  .owner__role { color: var(--forest-dark); font-weight: 700; font-size: 12px; }

  .contact {
    position: absolute;
    list-style: none;
    color: var(--ink-on-green);
    font-weight: 700;
    font-size: 16px;
  }
  .contact li { display: flex; align-items: center; gap: 10px; height: 30px; }
  .contact--direct { left: 24px; top: 216px; }
  .contact--social { right: 28px; top: 188px; }
  .icon {
    width: 22px; height: 22px; border-radius: 50%;
    background: var(--ink-on-green);
    display: flex; align-items: center; justify-content: center;
    flex: none;
  }
  .icon svg { width: 13px; height: 13px; }

  .website {
    position: absolute; right: 28px; bottom: 12px;
    color: var(--web-ink);
    font-weight: 700;
    font-size: 15px;
    letter-spacing: 5px;
  }
</style>
</head>
<body>

  <section class="card card--services" aria-label="Card side with services">
    <svg class="card__band" viewBox="0 0 540 309" preserveAspectRatio="none" aria-hidden="true">
      <path d="M0 222 Q300 214 540 150 L540 309 L0 309 Z" fill="var(--forest)"/>
      <path d="M0 232 Q300 224 540 160 L540 309 L0 309 Z" fill="var(--leaf)"/>
    </svg>
    <div class="brand"><span class="brand__dot"></span>Brookvale Yards</div>
    <p class="tagline">Serving Halifax &amp; Bedford for 5 years</p>
    <ul class="services">
      <li>Lawn Care</li>
      <li>Property Maintenance</li>
      <li>Garden Services</li>
    </ul>
  </section>

  <section class="card card--contact" aria-label="Card side with contact details">
    <svg class="card__band" viewBox="0 0 540 309" preserveAspectRatio="none" aria-hidden="true">
      <path d="M0 200 Q300 185 540 145 L540 309 L0 309 Z" fill="var(--forest)"/>
      <path d="M0 210 Q300 195 540 155 L540 309 L0 309 Z" fill="var(--leaf)"/>
    </svg>
    <div class="owner">
      <p class="owner__name">Morgan Pell</p>
      <p class="owner__role">Owner / Founder</p>
    </div>
    <div class="brand"><span class="brand__dot"></span>Brookvale Yards</div>

    <ul class="contact contact--social">
      <li><span class="icon"></span>/brookvaleyards</li>
      <li><span class="icon"></span>brookvaleyard</li>
    </ul>

    <ul class="contact contact--direct">
      <li>
        <span class="icon">
          <svg viewBox="0 0 24 24"><path fill="var(--leaf-deep)" d="M6.6 10.8a15 15 0 0 0 6.6 6.6l2.2-2.2a1 1 0 0 1 1-.25 11.4 11.4 0 0 0 3.6.57 1 1 0 0 1 1 1V20a1 1 0 0 1-1 1A17 17 0 0 1 3 4a1 1 0 0 1 1-1h3.5a1 1 0 0 1 1 1c0 1.25.2 2.45.57 3.6a1 1 0 0 1-.25 1z"/></svg>
        </span>902-555-0148
      </li>
      <li>
        <span class="icon">
          <svg viewBox="0 0 24 24"><rect x="3" y="6" width="18" height="12" rx="1.5" fill="none" stroke="var(--leaf-deep)" stroke-width="2"/><path d="M3.5 7l8.5 6 8.5-6" fill="none" stroke="var(--leaf-deep)" stroke-width="2"/></svg>
        </span>me@brookvaleyards.ca
      </li>
    </ul>

    <p class="website">www.brookvaleyards.ca</p>
  </section>

</body>
</html>
```